Vantoq Business Card Project showing the logo and a marbo image on the rear

Design a whacky but professional business card, the logo is for the front and the Marbo image is for the rear. Happy to consider other open source Marbo Images if the designer wants to select one from the web. Vantoq is a competitor to OMB.com.au and Pellory.com.au and is based around every property in Australia

Target Market(s)

Business

Contact Information for Business Card

Name, Title, Email, Web, Phone Number

Font styles to use
Other font styles liked:
• avenir

Requirements
Must have
• Image on Back logo on front
Nice to have
• Happy to consider other images on rear, preftably Colin Marbo. Image supplied I own, we can use open source other Marbo Images

```html
<!DOCTYPE html>
<html lang="en">
<head>
<meta charset="utf-8">
<title>Vantoq Business Card</title>
<link href="https://fonts.googleapis.com/css2?family=Nunito+Sans:wght@400;600;800&display=swap" rel="stylesheet">
<style>
  :root {
    --bg: #3a3a3c;
    --card: #ffffff;
    --orange: #f08a12;
    --ink: #1d1d1f;
    --grey: #4a4a4a;
    --sky: #2f8fd8;
    --night: #2546a8;
  }
  * { margin: 0; padding: 0; box-sizing: border-box; }
  html, body { width: 1200px; height: 900px; overflow: hidden; }
  body {
    background: var(--bg);
    font-family: "Nunito Sans", "Avenir", sans-serif;
    position: relative;
  }
  .card {
    position: absolute;
    left: 250px;
    width: 700px;
    height: 400px;
    border-radius: 26px;
    overflow: hidden;
  }
  .card--front { top: 36px; background: var(--card); }
  .card--back { top: 464px; }

  .brand {
    position: absolute; left: 56px; top: 52px;
    display: flex; align-items: center; gap: 14px;
  }
  .brand__mark { width: 34px; height: 34px; background: var(--orange); }
  .brand__name { font-weight: 800; font-size: 44px; color: var(--ink); letter-spacing: 0.5px; }

  .divider {
    position: absolute; left: 150px; right: 40px; top: 236px;
    height: 2px; background: var(--orange);
  }
  .person {
    position: absolute; right: 48px; top: 188px; text-align: right;
  }
  .person__name {
    font-size: 26px; font-weight: 400; color: var(--orange);
    letter-spacing: 1px; text-transform: uppercase;
  }
  .person__title {
    margin-top: 14px; font-size: 21px; color: var(--ink);
  }
  .contact {
    position: absolute; left: 40px; bottom: 40px;
    list-style: none; font-size: 19px; color: var(--grey); line-height: 1.35;
  }
  .contact li { display: flex; align-items: center; gap: 8px; }
  .contact svg { width: 12px; height: 12px; flex: none; }
  .edge-tab {
    position: absolute; right: 0; top: 300px; width: 10px; height: 44px;
    background: var(--orange);
  }
  .artwork {
    width: 100%; height: 100%;
    background:
      linear-gradient(180deg, transparent 40%, rgba(240,110,40,0.55) 70%, rgba(230,70,60,0.6) 100%),
      linear-gradient(90deg, var(--sky) 0%, #2a78d0 50%, var(--night) 100%);
  }
</style>
</head>
<body>
  <section class="card card--front">
    <div class="brand">
      <span class="brand__mark"></span>
      <span class="brand__name">Vantoq</span>
    </div>
    <div class="divider"></div>
    <div class="person">
      <p class="person__name">Tobias Wren</p>
      <p class="person__title">Director</p>
    </div>
    <ul class="contact">
      <li><svg viewBox="0 0 12 12"><path d="M2 1h3l1 3-1.5 1a6 6 0 0 0 2.5 2.5L8 6l3 1v3a1 1 0 0 1-1 1A9 9 0 0 1 1 2a1 1 0 0 1 1-1z" fill="var(--orange)"/></svg>555-014-2290</li>
      <li><svg viewBox="0 0 12 12"><rect x="1" y="2.5" width="10" height="7" fill="none" stroke="var(--orange)" stroke-width="1.4"/><path d="M1 3l5 3.5L11 3" fill="none" stroke="var(--orange)" stroke-width="1.2"/></svg>info@vantoq.com.au</li>
      <li><svg viewBox="0 0 12 12"><circle cx="6" cy="6" r="5" fill="var(--orange)"/></svg>www.vantoq.com.au</li>
    </ul>
    <div class="edge-tab"></div>
  </section>

  <section class="card card--back">
    <div class="artwork" role="img" aria-label="Colourful naive-style illustration of a crowded city of bright buildings under a blue sky with sun, clouds, stars and moon"></div>
  </section>
</body>
</html>
```